Automotive Accessories Business Card

Design a business template that match our new logo design and our industry.

https://www.qelmotorgear.com/

Target Market(s)

Aftermarket auto parts and accessories

Industry/Entity Type

automotive

Contact Information for Business Card

company logo

Font styles to use
Serif
Sans Serif

Colors
EB3D1F
EC4F4E
F09395
F8D3D4
FCEDEE

```html
<!DOCTYPE html>
<html lang="en">
<head>
<meta charset="utf-8">
<title>QEL Motor Gear Business Card</title>
<link href="https://fonts.googleapis.com/css2?family=Saira:wght@400;600;700&display=swap" rel="stylesheet">
<style>
  :root {
    --backdrop: #8f8f8f;
    --brand-red: #d92027;
    --ink-dark: #3c3c3c;
    --paper: #ffffff;
  }
  html, body {
    margin: 0;
    padding: 0;
    width: 1200px;
    height: 1200px;
    overflow: hidden;
    background: var(--backdrop);
    font-family: "Saira", sans-serif;
  }
  .card {
    position: absolute;
    left: 281px;
    width: 638px;
    height: 366px;
    border-radius: 19px;
    overflow: hidden;
    box-shadow: 3px 4px 6px rgba(0,0,0,0.35);
  }
  .card-front { top: 195px; background: var(--paper); }
  .card-back { top: 639px; background: var(--brand-red); }

  .wordmark {
    position: absolute;
    display: flex;
    align-items: center;
    font-weight: 700;
    white-space: nowrap;
    letter-spacing: 0.5px;
  }
  .wordmark .mark-square { display: inline-block; }
  .front-wordmark {
    left: 54px;
    top: 78px;
    font-size: 27px;
    color: var(--brand-red);
    gap: 10px;
  }
  .front-wordmark .mark-square { width: 18px; height: 18px; background: var(--brand-red); }
  .back-wordmark {
    left: 0;
    right: 0;
    top: 148px;
    justify-content: center;
    font-size: 50px;
    color: var(--paper);
    gap: 16px;
  }
  .back-wordmark .mark-square { width: 34px; height: 34px; background: var(--paper); }

  .side-bar {
    position: absolute;
    left: 0;
    top: 181px;
    width: 9px;
    height: 136px;
    background: var(--ink-dark);
  }

  .contact-list {
    position: absolute;
    left: 54px;
    top: 174px;
    margin: 0;
    padding: 0;
    list-style: none;
    color: var(--ink-dark);
    font-size: 15.5px;
    line-height: 21.6px;
    letter-spacing: 0.3px;
  }
  .contact-list li { display: flex; align-items: flex-start; }
  .contact-list li + li { margin-top: 8px; }
  .contact-list li.tight { margin-top: 0; }
  .contact-icon { width: 14px; height: 14px; margin: 4px 13px 0 0; flex: none; }

  .name-band {
    position: absolute;
    left: 331px;
    top: 208px;
    width: 307px;
    height: 80px;
    background: var(--brand-red);
    clip-path: polygon(76px 0, 100% 0, 100% 100%, 0 100%);
  }
  .name-block {
    position: absolute;
    right: 42px;
    top: 222px;
    text-align: right;
    color: var(--paper);
  }
  .person-name { margin: 0; font-size: 28px; font-weight: 600; line-height: 30px; letter-spacing: 1px; }
  .person-title { margin: 0; font-size: 16px; font-weight: 400; line-height: 18px; }
</style>
</head>
<body>
  <section class="card card-front">
    <div class="wordmark front-wordmark"><span class="mark-square"></span>QEL MOTOR GEAR</div>
    <div class="side-bar"></div>

    <ul class="contact-list">
      <li>
        <svg class="contact-icon" viewBox="0 0 14 14"><path d="M7 0a4.6 4.6 0 0 0-4.6 4.6C2.4 8 7 14 7 14s4.6-6 4.6-9.4A4.6 4.6 0 0 0 7 0zm0 6.4a1.8 1.8 0 1 1 0-3.6 1.8 1.8 0 0 1 0 3.6z" fill="var(--brand-red)"/></svg>
        <span>240 W. Harbor Ave. Unit B<br>Fontana, CA, 92335<br>United States</span>
      </li>
      <li>
        <svg class="contact-icon" viewBox="0 0 14 14"><path d="M3 1l2.3 2.8-1.2 1.6c.9 1.9 2.5 3.5 4.4 4.4l1.6-1.2L13 10.9 11.6 13C5.9 12.6 1.4 8.1 1 2.4z" fill="var(--brand-red)"/></svg>
        <span>1-800-555-0142</span>
      </li>
      <li class="tight">
        <svg class="contact-icon" viewBox="0 0 14 14"><rect x="0.5" y="3" width="13" height="9" fill="var(--brand-red)"/><path d="M0.5 3.5 7 8l6.5-4.5" stroke="#fff" stroke-width="1.2" fill="none"/></svg>
        <span>sales@qelmotorgear.com</span>
      </li>
      <li class="tight">
        <svg class="contact-icon" viewBox="0 0 14 14"><circle cx="7" cy="7" r="6.5" fill="var(--brand-red)"/><path d="M1 7h12M7 .5c-2.4 3.5-2.4 9.5 0 13M7 .5c2.4 3.5 2.4 9.5 0 13" stroke="#fff" stroke-width="1" fill="none"/></svg>
        <span>qelmotorgear.com</span>
      </li>
    </ul>

    <div class="name-band"></div>
    <div class="name-block">
      <p class="person-name">DANA REYES</p>
      <p class="person-title">Founder &amp; CEO</p>
    </div>
  </section>

  <section class="card card-back">
    <div class="wordmark back-wordmark"><span class="mark-square"></span>QEL MOTOR GEAR</div>
  </section>
</body>
</html>
```